Business Card Design Project

After recently finishing a design project for the company logo using markbazaar, it's now time for a business card. Attached to this is the logo.

The requirements for the business card are pretty straightforward:

- A clean, uncomplicated look
- Consistent usage of fonts
- Designs for both single sided and double sided cards
- A modern layout with preferably space to refer to social media accounts and/or downloadable vcards through a qr code
- consistent application of the company colour scheme: red/white. Hex codes for exact colour can be provided

Thanks!

```html
<!DOCTYPE html>
<html lang="en">
<head>
<meta charset="utf-8">
<title>Kilnstone Staffing – Business Card</title>
<link href="https://fonts.googleapis.com/css2?family=Source+Sans+3:wght@400;600;700&display=swap" rel="stylesheet">
<style>
  :root {
    --backdrop: #e8e5e1;
    --card: #ffffff;
    --ink: #231f20;
    --ink-soft: #3a3a3a;
    --brand-red: #e31e26;
    --swoosh-grey: #8a8a8a;
  }
  * { margin: 0; padding: 0; box-sizing: border-box; }
  html, body {
    width: 960px; height: 1200px; overflow: hidden;
    background: var(--backdrop);
    font-family: "Source Sans 3", "Myriad Pro", Arial, sans-serif;
    color: var(--ink);
  }
  .card {
    position: absolute;
    background: var(--card);
    border-radius: 30px;
    overflow: hidden;
    box-shadow: 0 6px 14px rgba(0,0,0,0.25);
  }
  .card--front { left: 57px; top: 100px; width: 838px; height: 478px; }
  .card--back  { left: 60px; top: 638px; width: 840px; height: 479px; }

  .brand {
    position: absolute;
    display: flex; align-items: center; gap: 22px;
    font-weight: 600; font-size: 66px; letter-spacing: -0.5px;
    color: var(--ink); white-space: nowrap;
  }
  .brand__mark { width: 58px; height: 58px; background: var(--brand-red); flex: none; }
  .card--front .brand { left: 150px; top: 105px; }
  .card--back .brand  { left: 146px; top: 126px; }

  .contact {
    position: absolute; left: 0; right: 0; top: 270px;
    text-align: center; color: var(--ink-soft);
  }
  .contact__name { font-size: 25px; font-weight: 700; color: var(--ink); }
  .contact__role { font-size: 21px; font-weight: 400; }
  .contact__line { font-size: 20px; margin-top: 14px; }
  .contact__line + .contact__line { margin-top: 8px; }
  .contact__label { font-weight: 700; font-style: italic; }
  .contact__sep { margin: 0 8px; }

  .swoosh { position: absolute; left: 0; bottom: 0; width: 838px; height: 478px; }
  .address {
    position: absolute; right: 73px; top: 442px;
    color: #ffffff; font-size: 21px;
  }
</style>
</head>
<body>
  <section class="card card--front">
    <div class="brand"><span class="brand__mark"></span>Kilnstone Staffing</div>

    <div class="contact">
      <p><span class="contact__name">Your Name -</span> <span class="contact__role">Designation</span></p>
      <p class="contact__line"><span class="contact__label">t</span> : 123-123-1234</p>
      <p class="contact__line">
        <span class="contact__label">e</span> : info@yourwebsite.com
        <span class="contact__sep">|</span>
        <span class="contact__label">w</span> : www.kilnstonestaffing.com
      </p>
    </div>

    <svg class="swoosh" viewBox="0 0 838 478" aria-hidden="true">
      <path d="M0,442 C140,428 300,416 430,412 C300,424 140,450 0,474 Z" fill="var(--swoosh-grey)"/>
      <path d="M0,478 L18,478 C140,452 300,426 440,414 C560,408 740,418 838,446 L838,478 Z" fill="var(--brand-red)"/>
    </svg>
    <p class="address">1234, Street Name, District, City, Country Code.</p>
  </section>

  <section class="card card--back">
    <div class="brand"><span class="brand__mark"></span>Kilnstone Staffing</div>
  </section>
</body>
</html>
```